13 Varno - new website design project

Our company Varno Electrical is developing a new lead generation website focused on Electrical, LED Lighting and Solar Power. We need a high converting website.

Example of our current website is www.varnoelectrical-example.com.au You can take content from this website for this new design. Our colours are red, black and white. For our new website we would like to promote Varno, Spark Every Day. Please listen to the jingle.

The below link is the company jingle that we have developed.
http://www.tunecraftdemo.com.au/vrn-tc-v1/

The key for this brief is to generate leads for Electrical, LED Lighting (for commercial) and Solar Power & Storage.

Target Market(s)

Business owners in Melbourne Victoria

Number of Pages Required

4 page

Colors
ec1f27
ffffff

Requirements
Must have
• This page must be clean, be in line with company branding and a high converting lead website.

```html
<!DOCTYPE html>
<html lang="en">
<head>
<meta charset="utf-8">
<title>Varno Electrical</title>
<link href="https://fonts.googleapis.com/css2?family=Barlow:wght@300;400;500;600;700&display=swap" rel="stylesheet">
<style>
:root{
  --red:#ec1f27;
  --ink:#1d1d1f;
  --body:#555;
  --white:#fff;
  --grey-bg:#f3f3f3;
  --line:#dcdcdc;
}
*{box-sizing:border-box;margin:0;padding:0}
html,body{width:1200px;height:3125px;overflow:hidden}
body{position:relative;font-family:"Barlow",Arial,sans-serif;color:var(--ink);background:var(--white)}
.btn{position:absolute;background:var(--red);color:var(--white);font-weight:600;font-size:10px;letter-spacing:.6px;text-transform:uppercase;display:flex;align-items:center;justify-content:center}
.section-title{position:absolute;left:0;width:1200px;text-align:center;font-weight:700;font-size:31px;letter-spacing:.3px;text-transform:uppercase;z-index:2}
.underline{position:absolute;left:555px;width:90px;height:4px;background:var(--red);z-index:2}

/* hero */
.hero{position:absolute;left:0;top:0;width:1200px;height:648px;background:linear-gradient(180deg,#2a3644 0%,#4a5868 45%,#33404c 72%,#1d2228 100%)}
.header{position:absolute;left:0;top:0;width:1200px;height:92px;background:rgba(10,14,18,.72);border-bottom:2px solid var(--red)}
.logo{position:absolute;left:222px;top:26px;font-weight:700;font-size:34px;color:var(--white);letter-spacing:1px}
.nav{position:absolute;left:0;top:42px;font-weight:600;font-size:12px;color:var(--white);text-transform:uppercase}
.nav span{position:absolute;white-space:nowrap}
.nav-marker{position:absolute;left:440px;top:83px;width:0;height:0;border-left:7px solid transparent;border-right:7px solid transparent;border-bottom:8px solid var(--red)}
.quick{position:absolute;left:872px;top:24px;font-size:9px;font-weight:600;color:var(--white);letter-spacing:.4px}
.phone{position:absolute;left:850px;top:46px;width:128px;height:26px;border-radius:13px;background:var(--red);color:var(--white);font-weight:600;font-size:16px;display:flex;align-items:center;justify-content:center;gap:6px}
.hero-title{position:absolute;left:218px;top:222px;font-weight:400;font-size:33px;line-height:38px;color:var(--white);text-transform:uppercase;letter-spacing:.5px}
.dots{position:absolute;display:flex;gap:8px}
.dots i{display:block;width:16px;height:5px;border-radius:3px;background:var(--white)}
.dots i.on{background:var(--red)}

/* services */
.service{position:absolute;top:692px;width:237px;height:160px;border-radius:4px;background:linear-gradient(160deg,#4a4d52,#2b2d31);display:flex;align-items:center;justify-content:center;box-shadow:0 1px 3px rgba(0,0,0,.3)}
.service-label{position:absolute;top:874px;width:237px;text-align:center;font-weight:600;font-size:15px;letter-spacing:.4px;text-transform:uppercase}

/* about */
.about{position:absolute;left:0;top:993px;width:1200px;height:459px;background:var(--grey-bg)}
.about-copy{position:absolute;left:170px;width:860px;text-align:center;font-size:11px;line-height:19px;color:var(--body)}

/* why */
.why-photo{position:absolute;left:222px;top:1670px;width:368px;height:195px;border:4px solid #ddd;background:linear-gradient(120deg,#8c949b,#c9cdd0 45%,#d98a3a 70%,#7b8288)}
.why-head{position:absolute;left:628px;top:1674px;font-weight:700;font-size:20px;color:var(--red);text-transform:uppercase}
.why-text{position:absolute;left:630px;top:1726px;width:320px;font-size:11.5px;line-height:21px;color:var(--body)}
.divider{position:absolute;left:220px;top:1905px;width:760px;height:1px;background:var(--line)}
.point{position:absolute;top:1930px;display:flex;gap:8px;font-weight:600;font-size:15px;line-height:20px;text-transform:uppercase}
.point b{color:var(--red)}

/* testimonials */
.testimonials{position:absolute;left:0;top:2072px;width:1200px;height:545px;background:var(--grey-bg)}
.client{position:absolute;left:0;width:1200px;text-align:center}
.client-name{top:2306px;font-size:40px;font-weight:400;color:#2a4ea8}
.client-person{top:2368px;font-size:20px;color:var(--body)}
.client-person strong{color:var(--red);font-weight:600}
.quote{top:2428px;font-size:22px;line-height:34px;color:#333;font-weight:400}

/* partners */
.partner{position:absolute;top:2677px;width:176px;height:88px;display:flex;align-items:center;justify-content:center;font-weight:600;font-size:20px}

/* footer */
.footer{position:absolute;left:0;top:2827px;width:1200px;height:298px;background:var(--grey-bg)}
.footer-logo{position:absolute;left:170px;top:2862px;font-weight:700;font-size:38px;color:var(--ink);letter-spacing:1px}
.col{position:absolute;top:2884px;font-size:11.5px;line-height:24px;text-transform:uppercase;color:#333}
.col h4{font-size:11.5px;font-weight:600;color:var(--red);margin-bottom:24px}
.bottom-rule{position:absolute;left:0;top:3074px;width:1200px;height:1px;background:var(--line)}
.copyright{position:absolute;left:182px;top:3090px;font-size:11px;color:#333}
.copyright strong{color:var(--red);font-weight:600}
.social{position:absolute;top:3090px;width:11px;height:11px}
</style>
</head>
<body>

<!-- Hero -->
<div class="hero" role="img" aria-label="Worker silhouette facing high-voltage transmission towers under a dusk sky"></div>
<header class="header">
  <div class="logo">VARNO</div>
  <nav class="nav">
    <span style="left:430px">Home</span>
    <span style="left:508px">Varno Story</span>
    <span style="left:622px">Our Work</span>
    <span style="left:727px">Contact Us</span>
  </nav>
  <div class="nav-marker"></div>
  <div class="quick">QUICK CALL NOW !</div>
  <div class="phone">
    <svg width="12" height="12" viewBox="0 0 24 24"><path fill="#fff" d="M6.6 10.8c1.4 2.8 3.8 5.1 6.6 6.6l2.2-2.2c.3-.3.7-.4 1-.2 1.1.4 2.3.6 3.6.6.6 0 1 .4 1 1V20c0 .6-.4 1-1 1C10.6 21 3 13.4 3 4c0-.6.4-1 1-1h3.5c.6 0 1 .4 1 1 0 1.3.2 2.5.6 3.6.1.3 0 .7-.2 1L6.6 10.8z"/></svg>
    130047VARNO
  </div>
</header>
<h1 class="hero-title">Australia Largest<br>Fully Integrated<br>Electrical &amp;<br>Energy Solutions<br>Provider</h1>
<div class="btn" style="left:220px;top:435px;width:146px;height:40px">Learn More</div>
<div class="dots" style="left:220px;top:528px"><i class="on"></i><i></i><i></i><i></i></div>

<!-- Services -->
<div class="service" style="left:222px">
  <svg width="60" height="80" viewBox="0 0 60 80" fill="none" stroke="#ec1f27" stroke-width="3"><path d="M30 4 L12 76 M30 4 L48 76 M6 22 H54 M10 40 H50 M18 22 L42 40 M42 22 L18 40 M16 58 H44 M20 40 L40 58 M40 40 L20 58"/></svg>
</div>
<div class="service-label" style="left:222px">Electrical</div>
<div class="service" style="left:481px">
  <svg width="40" height="80" viewBox="0 0 40 80" fill="none" stroke="#fff" stroke-width="3"><rect x="6" y="4" width="28" height="44" rx="14"/><path d="M12 16 V40 M20 12 V40 M28 16 V40"/><rect x="12" y="50" width="16" height="14"/><path d="M16 64 V74 H24 V64"/></svg>
</div>
<div class="service-label" style="left:481px">LED Lighting</div>
<div class="service" style="left:741px">
  <svg width="50" height="84" viewBox="0 0 50 84" fill="none" stroke="#fff" stroke-width="3" stroke-linejoin="round"><path d="M30 2 L6 46 H24 L16 82 L44 32 H26 Z"/></svg>
</div>
<div class="service-label" style="left:741px">Solar Power</div>

<!-- About -->
<section class="about"></section>
<h2 class="section-title" style="top:1058px">About Us</h2>
<div class="underline" style="top:1101px"></div>
<p class="about-copy" style="top:1168px">Electrical and Energy Solutions are at the forefront of our company. Varno Electrical has a long history in Electrical, LED Lighting and Solar Power and just like the Cougar, we will strive to be fierce &amp; agile in an effort to exceed our customer's expectations and develop stronger links with all our business partners &amp; community.</p>
<p class="about-copy" style="top:1223px">Varno Electrical is an expert Electrical Company providing services to all Residential and Commercial customers. With over 10 years of experience, Varno Electrical has developed a highly-experienced team of professionals that ensure all our customer expectations are exceeded. Our team comprise of over 70 staff of Designers, Consultants, Electricians who provide expert advice and quality of installation at an affordable price.</p>
<div class="btn" style="left:525px;top:1330px;width:150px;height:45px">Learn More</div>

<!-- Why choose us -->
<h2 class="section-title" style="top:1568px">Why Choose Us?</h2>
<div class="underline" style="top:1612px"></div>
<div class="why-photo" role="img" aria-label="Electrician in hard hat and hi-vis vest at a substation"></div>
<div class="why-head">1. Professional Service</div>
<p class="why-text">When you hire a Varno Electrical Electrician you will get a professional and well-presented Electrician that comes skilled and ready to do the job.</p>
<div class="btn" style="left:630px;top:1817px;width:105px;height:38px">Learn More</div>
<div class="divider"></div>
<div class="point" style="left:220px"><b>2.</b><span>5 Year<br>Workmanship<br>Guarantee</span></div>
<div class="point" style="left:417px"><b>3.</b><span>Value For<br>Money</span></div>
<div class="point" style="left:606px"><b>4.</b><span>Environmentally<br>Friendly</span></div>
<div class="point" style="left:803px"><b>5.</b><span>Fully<br>Insured</span></div>

<!-- Testimonials -->
<section class="testimonials"></section>
<h2 class="section-title" style="top:2185px">Testimonials</h2>
<div class="underline" style="top:2247px"></div>
<div class="client client-name">Brightvale</div>
<div class="client client-person"><strong>R. Delmar</strong> | Balwyn North VIC</div>
<p class="client quote">They clean up after the job, explained everything I needed to know and answered all<br>questions, very professional. Will use them again in the future!</p>
<div class="dots" style="left:540px;top:2538px"><i class="on" style="width:18px"></i><i style="background:#ccc;width:18px"></i><i style="background:#ccc;width:18px"></i><i style="background:#ccc;width:18px"></i></div>

<!-- Partners -->
<div class="partner" style="left:220px;background:#ffe600;color:#1d1d1f">Outback Supply</div>
<div class="partner" style="left:415px;background:#ec3a2e;color:#fff">Heron</div>
<div class="partner" style="left:609px;background:#d6121b;color:#fff">Golden Grill</div>
<div class="partner" style="left:804px;background:#2b3593;color:#fff">Brightvale</div>

<!-- Footer -->
<footer class="footer"></footer>
<div class="footer-logo">VARNO</div>
<div class="col" style="left:423px"><h4>Menu Links</h4>Home<br>Varno Story<br>Our Work<br>Contact Us</div>
<div class="col" style="left:632px"><h4>Quick Links</h4>LED Lighting<br>Solar Power<br>Electrical<br>Career</div>
<div class="col" style="left:843px"><h4>Other Links</h4>Terms and Conditions<br>Privacy</div>
<div class="bottom-rule"></div>
<div class="copyright">© 2017 <strong>VARNO ELECTRICAL</strong> | All Rights Reserved</div>
<svg class="social" style="left:906px" viewBox="0 0 10 10"><rect width="10" height="10" rx="2" fill="#ec1f27"/></svg>
<svg class="social" style="left:934px" viewBox="0 0 10 10"><rect width="10" height="10" rx="2" fill="#333"/></svg>
<svg class="social" style="left:962px" viewBox="0 0 10 10"><rect width="10" height="10" rx="2" fill="#333"/></svg>

</body>
</html>
```